Biobased Flyer Final touchups

I'm attaching the current ad that we need to finish up.
The target audience for this flyer are industrialist developing biobased products, a type of "green" or eco product. We provide a test that measures how much biobased vs petroleum (fossil) content their product has. We are trying to encourage product developers to test because consumers care about the biobased content. Our ad, a customer with a shopping cart full of biobased products, reflects the demand/interest for this products.
For our ad, we would like to improve the back of the aisles where petroleum based products are. One of the ideas I had in mind, was to make the shelves leak petroleum to make it clear that those are that and that they are dirty. I'm open to other ideas.
The main purpose of the project is to fix the background, we think that is the only thing that needs improvements before we use this. However, if you have more ideas we certainly welcome them.
Here is more info on what we do to give you a clearer idea of the purpose of the ad.
http://www.qorvinanalytics.com/biobased.html
Let me know if you are interested. I can send you the PSD file as requested.
Marisol
The target are industrialist working on developing biobased products and applying for green certifications.
Shopping

```html
<!DOCTYPE html>
<html lang="en">
<head>
<meta charset="UTF-8">
<title>Consumers Crave Biobased – Qorvin Analytics</title>
<link rel="stylesheet" href="https://fonts.googleapis.com/css2?family=Arimo:wght@400;700&family=Open+Sans:wght@400;600&display=swap">
<style>
  :root {
    --ink: #1f1f1f;
    --red: #c11f2c;
    --blue: #1a6fc4;
    --blue-light: #3aa5e0;
    --navy: #28327a;
    --leaf-soft: rgba(108, 191, 58, 0.45);
    --paper-edge: #e4e9ef;
    --paper-centre: #fbfcfd;
    --white: #ffffff;
  }
  * { margin: 0; padding: 0; box-sizing: border-box; }
  html, body { width: 954px; height: 1200px; overflow: hidden; background: var(--white); }
  .flyer {
    position: relative;
    width: 954px;
    height: 1200px;
    overflow: hidden;
    background: radial-gradient(ellipse at 55% 45%, var(--paper-centre) 0%, var(--paper-centre) 35%, var(--paper-edge) 100%);
    font-family: "Arimo", Arial, sans-serif;
    color: var(--ink);
  }
  .brand {
    position: absolute;
    left: 76px; top: 59px;
    width: 161px; height: 112px;
    background: var(--white);
    border-radius: 8px;
    display: flex; align-items: center; justify-content: center;
    gap: 8px;
  }
  .brand-square { width: 18px; height: 18px; background: var(--red); }
  .brand-name { font-weight: 700; font-size: 19px; line-height: 1.1; color: var(--ink); }
  .site-url {
    position: absolute;
    right: 69px; top: 89px;
    font-family: "Open Sans", Arial, sans-serif;
    font-size: 28px;
    color: var(--ink);
  }
  .top-wave { position: absolute; left: 0; top: 150px; width: 954px; height: 80px; }
  .leaf-top {
    position: absolute; left: 704px; top: 150px; width: 104px; height: 78px;
    background: radial-gradient(ellipse at 50% 50%, var(--leaf-soft) 0%, rgba(108,191,58,0.2) 50%, rgba(108,191,58,0) 72%);
  }
  .headline {
    position: absolute; left: 0; right: 0; top: 238px;
    text-align: center;
    font-size: 50px; line-height: 1; font-weight: 700; letter-spacing: 0.3px;
    color: var(--ink);
  }
  .hero-scene {
    position: absolute; left: 146px; top: 326px; width: 682px; height: 503px;
    border-radius: 28px;
    background:
      radial-gradient(ellipse at 50% 50%, rgba(251,252,253,0) 55%, rgba(240,244,248,0.9) 100%),
      linear-gradient(90deg, rgba(40,40,40,0.42) 0%, rgba(45,45,45,0.32) 45%, rgba(90,170,70,0.28) 62%, rgba(47,127,208,0.28) 78%, rgba(90,170,70,0.24) 100%);
  }
  .cta { position: absolute; left: 381px; top: 873px; }
  .cta-title { font-size: 35px; font-weight: 700; line-height: 42px; color: var(--ink); margin-bottom: 6px; }
  .cta-list { list-style: none; }
  .cta-list li {
    display: flex; align-items: center; gap: 8px;
    font-size: 27px; font-weight: 700; color: var(--red);
    height: 44px;
  }
  .cta-list svg { flex: none; }
  .bottom-wave { position: absolute; left: 0; top: 1010px; width: 954px; height: 190px; }
  .leaf-bottom {
    position: absolute; left: 756px; top: 1052px; width: 162px; height: 96px;
    background: radial-gradient(ellipse at 50% 50%, var(--leaf-soft) 0%, rgba(108,191,58,0.2) 50%, rgba(108,191,58,0) 72%);
  }
  .footer-bar {
    position: absolute; left: 0; right: 0; top: 1152px;
    display: flex; justify-content: center; align-items: center;
    font-family: "Open Sans", Arial, sans-serif;
    color: var(--white);
  }
  .footer-main { font-size: 25px; font-weight: 600; }
  .footer-divider { width: 2px; height: 28px; background: var(--white); margin: 0 12px; }
  .footer-note { font-size: 20px; font-weight: 400; }
</style>
</head>
<body>
<main class="flyer">
  <div class="brand"><span class="brand-square"></span><span class="brand-name">Qorvin<br>Analytics</span></div>
  <div class="site-url">www.qorvinanalytics.com</div>

  <svg class="top-wave" viewBox="0 0 954 80" aria-hidden="true">
    <path d="M34 64 C 250 86, 520 30, 700 38 C 790 42, 860 56, 920 70 C 860 50, 790 30, 700 28 C 520 22, 250 78, 34 64 Z" fill="var(--blue)"/>
  </svg>
  <div class="leaf-top" role="img" aria-label="Green leaf with a water droplet"></div>

  <h1 class="headline">CONSUMERS CRAVE BIOBASED</h1>

  <div class="hero-scene" role="img" aria-label="Stacked black oil barrels leaking onto the floor beside a blue figure pushing shopping carts full of green boxes labelled 85% and 92% biobased"></div>

  <section class="cta">
    <h2 class="cta-title">Test Your Biobased Content</h2>
    <ul class="cta-list">
      <li><svg width="22" height="20" viewBox="0 0 22 20"><rect x="1" y="4" width="14" height="14" fill="none" stroke="var(--ink)" stroke-width="2"/><path d="M4 10 L8 14 L20 1" fill="none" stroke="var(--ink)" stroke-width="2.5"/></svg>For biobased product development</li>
      <li><svg width="22" height="20" viewBox="0 0 22 20"><rect x="1" y="4" width="14" height="14" fill="none" stroke="var(--ink)" stroke-width="2"/><path d="M4 10 L8 14 L20 1" fill="none" stroke="var(--ink)" stroke-width="2.5"/></svg>To attain biobased product labels</li>
      <li><svg width="22" height="20" viewBox="0 0 22 20"><rect x="1" y="4" width="14" height="14" fill="none" stroke="var(--ink)" stroke-width="2"/><path d="M4 10 L8 14 L20 1" fill="none" stroke="var(--ink)" stroke-width="2.5"/></svg>To verify claims to consumers</li>
    </ul>
  </section>

  <svg class="bottom-wave" viewBox="0 0 954 190" preserveAspectRatio="none" aria-hidden="true">
    <defs>
      <linearGradient id="navyBand" x1="0" x2="1" y1="0" y2="0">
        <stop offset="0" stop-color="#262d72"/>
        <stop offset="0.6" stop-color="#2a3a8a"/>
        <stop offset="1" stop-color="#3aa5e0"/>
      </linearGradient>
    </defs>
    <path d="M0 40 C 150 0, 300 20, 480 70 C 650 115, 820 110, 954 80 L954 190 L0 190 Z" fill="var(--blue-light)"/>
    <path d="M0 60 C 160 20, 320 45, 500 95 C 660 135, 820 125, 954 100 L954 190 L0 190 Z" fill="var(--blue)"/>
    <path d="M0 85 C 170 55, 340 80, 520 120 C 680 150, 830 140, 954 120 L954 190 L0 190 Z" fill="#d6e8f5"/>
    <path d="M0 100 C 180 75, 350 100, 530 132 C 690 158, 840 150, 954 135 L954 190 L0 190 Z" fill="url(#navyBand)"/>
  </svg>
  <div class="leaf-bottom" role="img" aria-label="Pair of green leaves with water droplets"></div>

  <footer class="footer-bar">
    <span class="footer-main">ISO 17025 Accredited Biobased Testing Lab</span>
    <span class="footer-divider"></span>
    <span class="footer-note">Test Results in 3-5 Business days</span>
  </footer>
</main>
</body>
</html>
```